New bussiness card, using company logo.
Lionel Brisk
Manager/Director
Brisk Property Developments
Po Box 5347
Wattlebrook Central
Qld
0491 638 205
lionel@briskpropertydevelopments
eye catching, vibrant colours, professional

```html
<!DOCTYPE html>
<html lang="en">
<head>
<meta charset="utf-8">
<title>Brisk Property Developments – Business Cards</title>
<link href="https://fonts.googleapis.com/css2?family=Jost:wght@400;500;700&display=swap" rel="stylesheet">
<style>
  :root {
    --backdrop: #2b2830;
    --card-white: #ffffff;
    --brand-green: #6cb944;
    --brand-green-light: #8cc63f;
    --brand-red: #dd2a30;
    --ink: #3a3a3a;
    --rule-grey: #bdbdbd;
  }
  * { box-sizing: border-box; margin: 0; padding: 0; }
  html, body {
    width: 1200px; height: 767px; overflow: hidden;
    background: var(--backdrop);
    font-family: "Jost", Arial, sans-serif;
  }
  .sheet { position: relative; width: 1200px; height: 767px; }

  .card {
    position: absolute;
    width: 525px; height: 300px;
    border-radius: 20px;
    overflow: hidden;
    box-shadow: 0 3px 10px rgba(0,0,0,.45);
  }
  .card--contact { left: 42px; top: 44px; background: var(--card-white); }
  .card--logo-white { left: 607px; top: 48px; background: var(--card-white); }
  .card--logo-green { left: 44px; top: 396px; background: linear-gradient(180deg, var(--brand-green) 0%, var(--brand-green-light) 100%); }
  .card--logo-red { left: 623px; top: 403px; background: var(--brand-red); }

  /* contact card */
  .hairline { position: absolute; left: 0; right: 0; height: 1px; background: var(--brand-red); opacity: .7; }
  .hairline--top-a { top: 33px; }
  .hairline--top-b { top: 37px; background: var(--rule-grey); }
  .hairline--bottom { top: 95px; }
  .name-band {
    position: absolute; left: 0; right: 0; top: 40px; height: 46px;
    background: linear-gradient(90deg, var(--brand-green) 0%, var(--brand-green-light) 100%);
    display: flex; align-items: center; justify-content: center;
    color: #fff;
  }
  .name-band__name { font-weight: 700; font-size: 19px; }
  .name-band__role { font-weight: 400; font-size: 16px; margin-left: 6px; }

  .brand-lockup {
    position: absolute;
    display: flex; align-items: center; gap: 12px;
    width: max-content;
    transform: translate(-50%, -50%);
    font-weight: 700; text-transform: uppercase;
  }
  .brand-lockup__mark { flex: none; }
  .brand-lockup__name { text-align: center; line-height: 1.05; letter-spacing: .5px; }

  .card--contact .brand-lockup { left: 130px; top: 192px; gap: 8px; }
  .card--contact .brand-lockup__mark { width: 14px; height: 14px; background: var(--brand-green); }
  .card--contact .brand-lockup__name { color: var(--brand-red); font-size: 21px; }

  .divider { position: absolute; left: 258px; top: 140px; width: 1px; height: 112px; background: var(--rule-grey); }

  .contact-list { position: absolute; left: 272px; top: 146px; list-style: none; color: var(--ink); font-size: 13.5px; line-height: 17px; }
  .contact-list li { display: flex; align-items: flex-start; gap: 7px; }
  .contact-list li + li { margin-top: 15px; }
  .contact-list svg { flex: none; margin-top: 3px; fill: var(--brand-green); }
  .contact-list__phone { font-size: 15px; }
  .contact-list__email { font-size: 12.5px; }

  /* logo cards */
  .card--logo-white .brand-lockup { left: 50%; top: 140px; }
  .card--logo-green .brand-lockup { left: 50%; top: 138px; }
  .card--logo-red .brand-lockup { left: 50%; top: 136px; }
  .card--logo-white .brand-lockup__mark { width: 22px; height: 22px; background: var(--brand-green); }
  .card--logo-white .brand-lockup__name { color: var(--brand-red); font-size: 40px; }
  .card--logo-green .brand-lockup__mark,
  .card--logo-red .brand-lockup__mark { width: 22px; height: 22px; background: #fff; }
  .card--logo-green .brand-lockup__name,
  .card--logo-red .brand-lockup__name { color: #fff; font-size: 40px; }

  .web-address {
    position: absolute; left: 0; right: 0;
    text-align: center; font-size: 14px; font-weight: 500; letter-spacing: 2.6px;
  }
  .card--logo-white .web-address { top: 264px; color: var(--ink); }
  .web-address__domain--red { color: var(--brand-red); }
  .web-address__domain--green { color: var(--brand-green); }
  .card--logo-green .web-address { top: 252px; color: #fff; }
  .card--logo-red .web-address { top: 252px; color: #fff; }
</style>
</head>
<body>
<main class="sheet">

  <section class="card card--contact" aria-label="Business card front">
    <div class="hairline hairline--top-a"></div>
    <div class="hairline hairline--top-b"></div>
    <div class="name-band">
      <span class="name-band__name">Lionel Brisk,</span>
      <span class="name-band__role">Manager/Director</span>
    </div>
    <div class="hairline hairline--bottom"></div>

    <div class="brand-lockup">
      <span class="brand-lockup__mark"></span>
      <span class="brand-lockup__name">Brisk Property<br>Developments</span>
    </div>

    <div class="divider"></div>

    <ul class="contact-list">
      <li>
        <svg width="11" height="11" viewBox="0 0 12 12" aria-hidden="true"><path d="M6 0 12 6H10V12H7.5V8.5H4.5V12H2V6H0Z"/></svg>
        <span>Po Box 5347<br>Wattlebrook Central , Qld</span>
      </li>
      <li>
        <svg width="10" height="11" viewBox="0 0 12 12" aria-hidden="true"><path d="M2.5 0 4.8 3 3.5 4.6C4.4 6.6 5.6 7.9 7.4 8.6L9 7.2 12 9.5 10.3 11.8C5.5 11.5.5 6.5.2 1.7Z"/></svg>
        <span class="contact-list__phone">0491 638 205</span>
      </li>
      <li>
        <svg width="11" height="9" viewBox="0 0 12 9" aria-hidden="true"><path d="M0 0H12V1.2L6 5 0 1.2ZM0 2.6 6 6.4 12 2.6V9H0Z"/></svg>
        <span class="contact-list__email">lionel@briskpropertydevelopments.com</span>
      </li>
    </ul>
  </section>

  <section class="card card--logo-white" aria-label="Business card back, white">
    <div class="brand-lockup">
      <span class="brand-lockup__mark"></span>
      <span class="brand-lockup__name">Brisk Property<br>Developments</span>
    </div>
    <p class="web-address">www.<span class="web-address__domain--red">brisk</span><span class="web-address__domain--green">propertydevelopments</span>.com</p>
  </section>

  <section class="card card--logo-green" aria-label="Business card back, green">
    <div class="brand-lockup">
      <span class="brand-lockup__mark"></span>
      <span class="brand-lockup__name">Brisk Property<br>Developments</span>
    </div>
    <p class="web-address">www.briskpropertydevelopments.com</p>
  </section>

  <section class="card card--logo-red" aria-label="Business card back, red">
    <div class="brand-lockup">
      <span class="brand-lockup__mark"></span>
      <span class="brand-lockup__name">Brisk Property<br>Developments</span>
    </div>
    <p class="web-address">www.briskpropertydevelopments.com</p>
  </section>

</main>
</body>
</html>
```